Business Card Re-Design/Update

We'd like to update out business cards. I've included our current "Style guide" which has the colour scheme of the organisation in it. I've also included the branding files with logos etc in them.

I've also included a copy of one of our existing cards so that you can see how ugly/dated they look. I'd like a fresh modern corporate look.

Target Market(s)

These are for our clients, potential clients, industry contacts - like all business cards

Contact Information for Business Card

Name
Position
Company Address - Level 1, 47 Fernby Street, Carlow Qld 4072
Direct Phone
mobile
Email
Website -www.korvalit.com.au
Logo

Colors

Designer to choose colors to be used in the design.

Requirements
Must have
• Main Logo
• Cards will need to be editable to be able to personalize them for each new employee.
Nice to have
• The MapOut, ShipWell, KeepSteady would be okay to have if they can be sensibly and professionally added to the look without detracting from the main imagery.
• Maybe they could go on the back of the card? will leave this to your creative discretion as to whether/where they fit.
Should not have
• Should not have decorative or script fonts

```html
<!DOCTYPE html>
<html lang="en">
<head>
<meta charset="utf-8">
<title>korvalIT business card</title>
<link rel="stylesheet" href="https://fonts.googleapis.com/css2?family=Arimo:wght@400;700&display=swap">
<style>
  :root {
    --brand-red: #d71920;
    --ink: #333333;
    --ink-soft: #555555;
    --rule: #c9c9c9;
    --paper: #ffffff;
    --backdrop: #3a3430;
    --ship-blue: #1e88d2;
    --map-green: #5aa433;
    --keep-magenta: #b8258e;
  }
  * { box-sizing: border-box; margin: 0; padding: 0; }
  html, body { width: 1200px; height: 844px; overflow: hidden; }
  body {
    background: var(--backdrop);
    font-family: "Arimo", Arial, sans-serif;
    position: relative;
  }
  .card {
    position: absolute;
    width: 500px;
    height: 290px;
    background: var(--paper);
    box-shadow: 0 10px 30px rgba(0,0,0,.45);
    overflow: hidden;
  }
  .card--front { left: 70px; top: 277px; }
  .card--back { left: 630px; top: 277px; }

  /* front */
  .brand {
    display: flex;
    align-items: center;
    gap: 10px;
    font-weight: 700;
    letter-spacing: -0.5px;
  }
  .brand__mark { display: block; }
  .front-brand {
    position: absolute;
    right: 40px;
    top: 34px;
    font-size: 34px;
    color: var(--ink);
  }
  .front-brand .brand__mark { width: 26px; height: 26px; background: var(--brand-red); }
  .rule {
    position: absolute;
    left: 28px;
    right: 28px;
    height: 1px;
    background: var(--rule);
  }
  .rule--a { top: 96px; left: 240px; }
  .rule--b { top: 118px; left: 240px; }
  .person { position: absolute; left: 28px; top: 138px; }
  .person__name {
    color: var(--brand-red);
    font-weight: 700;
    font-size: 17px;
    letter-spacing: .3px;
    text-transform: uppercase;
  }
  .person__role { color: var(--ink-soft); font-size: 14px; margin-top: 2px; }
  .rule--c { top: 184px; right: 200px; }
  .address { position: absolute; left: 28px; top: 194px; color: var(--ink-soft); font-size: 14px; }
  .rule--d { top: 220px; right: 200px; }
  .contacts {
    position: absolute;
    left: 28px;
    top: 232px;
    display: flex;
    gap: 14px;
    font-size: 13.5px;
    color: var(--ink);
    line-height: 1.4;
  }
  .contacts__col + .contacts__col { border-left: 1px solid var(--ink-soft); padding-left: 14px; }
  .contacts__label { color: var(--brand-red); font-weight: 700; }

  /* back */
  .back-band {
    position: absolute;
    inset: 0 0 95px 0;
    background: var(--brand-red);
    display: flex;
    flex-direction: column;
    align-items: center;
    justify-content: center;
    gap: 12px;
  }
  .back-brand { font-size: 40px; color: var(--paper); }
  .back-brand .brand__mark { width: 30px; height: 30px; background: var(--paper); }
  .back-url { color: var(--paper); font-size: 12px; font-weight: 700; letter-spacing: .4px; }
  .services {
    position: absolute;
    left: 0; right: 0; bottom: 0;
    height: 95px;
    display: flex;
    align-items: center;
    justify-content: center;
    gap: 22px;
  }
  .service { display: flex; align-items: center; gap: 6px; font-size: 21px; font-weight: 400; }
  .service__mark { width: 14px; height: 14px; }
  .service--ship { color: var(--ship-blue); }
  .service--ship .service__mark { background: var(--ship-blue); }
  .service--map { color: var(--map-green); }
  .service--map .service__mark { background: var(--map-green); }
  .service--keep { color: var(--keep-magenta); }
  .service--keep .service__mark { background: var(--keep-magenta); }
</style>
</head>
<body>
  <section class="card card--front" aria-label="Card front">
    <div class="brand front-brand"><span class="brand__mark"></span><span>korvalIT</span></div>
    <div class="rule rule--a"></div>
    <div class="rule rule--b"></div>
    <div class="person">
      <p class="person__name">Maren Holt</p>
      <p class="person__role">Business Development Manager</p>
    </div>
    <div class="rule rule--c"></div>
    <p class="address">Level 1, 47 Fernby Street, Carlow Qld 4072</p>
    <div class="rule rule--d"></div>
    <div class="contacts">
      <div class="contacts__col">
        <p><span class="contacts__label">P:</span> +61 (0)400 555 017</p>
        <p><span class="contacts__label">F:</span> +61 (0)7 5550 1203</p>
      </div>
      <div class="contacts__col">
        <p><span class="contacts__label">M:</span> +61 (0)7 5550 1233</p>
        <p><span class="contacts__label">E:</span> mholt@korvalit.com.au</p>
      </div>
    </div>
  </section>

  <section class="card card--back" aria-label="Card back">
    <div class="back-band">
      <div class="brand back-brand"><span class="brand__mark"></span><span>korvalIT</span></div>
      <p class="back-url">www.korvalit.com.au</p>
    </div>
    <div class="services">
      <p class="service service--ship"><span class="service__mark"></span>ShipWell</p>
      <p class="service service--map"><span class="service__mark"></span>MapOut</p>
      <p class="service service--keep"><span class="service__mark"></span>KeepSteady</p>
    </div>
  </section>
</body>
</html>
```